Home Loan Introducer needs logo/business cards

We need a simple but classy logo for business cards and flyers. The business is a home loan referral business that is called an Introducer. The business name is "The Harborline".
I was thinking very simple and straight to the point on the front with "Home Loans" the only thing on the front with a nice background colour/s.
Then on the back, "The Harborline"
and "Quality Customer Service"
and "Email, text or call welcome"
and then my name, email address and phone number.
Updates
Thank you for all the designs :-)
Target Market(s)
Home buyers.
Home owners.
Investors.
Industry/Entity Type
Loan
Look and feel

```html
<!DOCTYPE html>
<html lang="en">
<head>
<meta charset="utf-8">
<title>The Harborline – Business Cards</title>
<link rel="stylesheet" href="https://fonts.googleapis.com/css2?family=Exo+2:wght@500;600;700;800&display=swap">
<style>
  :root {
    --page-bg: #e9e6e1;
    --brand-blue: #0b6cb6;
    --deep-blue: #0b5aa3;
    --soft-blue: #3f8ccb;
    --brand-orange: #fbb03f;
    --pale-orange: #fde1b0;
    --white: #ffffff;
    --rule: #ffffff;
  }
  * { box-sizing: border-box; margin: 0; padding: 0; }
  html, body {
    width: 1200px; height: 750px; overflow: hidden;
    background: var(--page-bg);
    font-family: "Exo 2", "Trebuchet MS", sans-serif;
  }
  .stage { position: relative; width: 1200px; height: 750px; }

  .card {
    position: absolute; top: 215px;
    width: 540px; height: 320px;
    overflow: hidden;
    box-shadow: 0 10px 24px rgba(0,0,0,0.22);
  }

  /* Front */
  .card-front { left: 40px; background: var(--brand-blue); }
  .front-houses {
    position: absolute; left: 60px; top: 40px;
    width: 300px; height: 130px;
    background: linear-gradient(180deg, rgba(255,255,255,0.10), rgba(255,255,255,0.22));
    border-radius: 6px;
  }
  .front-band {
    position: absolute; left: 40px; top: 160px;
    width: 460px; height: 96px;
    background: var(--brand-orange);
    border-radius: 10px;
    display: flex; align-items: center; justify-content: center;
    font-weight: 800; font-size: 64px; letter-spacing: 1px;
    text-transform: uppercase;
  }
  .front-band .word-home { color: var(--white); margin-right: 18px; }
  .front-band .word-loan { color: var(--deep-blue); }

  /* Back */
  .card-back { left: 620px; background: var(--white); }
  .back-lower {
    position: absolute; left: 0; right: 0; bottom: 0; height: 190px;
    background: var(--brand-orange);
  }
  .back-house {
    position: absolute; left: 30px; bottom: 0;
    width: 220px; height: 175px;
    background: linear-gradient(180deg, var(--pale-orange), #fcd38c);
    border-radius: 8px 8px 0 0;
  }
  .brand {
    position: absolute; left: 130px; top: 36px; width: 310px;
    display: flex; flex-direction: column; align-items: center; gap: 12px;
  }
  .brand-dot {
    width: 58px; height: 58px; border-radius: 50%;
    background: var(--brand-blue);
  }
  .brand-name {
    width: 100%; padding: 5px 0;
    background: var(--brand-orange); border-radius: 4px;
    text-align: center;
    font-weight: 700; font-size: 26px; letter-spacing: 1px;
    color: var(--deep-blue); text-transform: uppercase;
  }
  .details {
    position: absolute; right: 28px; top: 168px; width: 210px;
    color: var(--deep-blue);
  }
  .perks { list-style: none; font-size: 14px; font-weight: 600; line-height: 1.45; }
  .perks li { display: flex; align-items: center; gap: 5px; white-space: nowrap; }
  .perks svg { width: 13px; height: 13px; flex: none; }
  .person {
    margin-top: 14px; text-align: center;
    font-size: 21px; font-weight: 600;
    padding-bottom: 5px; border-bottom: 2px solid var(--rule);
  }
  .contact {
    margin-top: 6px; text-align: center;
    font-size: 10.5px; color: var(--white); line-height: 1.4;
  }
</style>
</head>
<body>
<main class="stage">
  <section class="card card-front" aria-label="Business card front">
    <div class="front-houses" role="img" aria-label="Row of three faint house illustrations"></div>
    <h1 class="front-band"><span class="word-home">Home</span><span class="word-loan">Loan</span></h1>
  </section>

  <section class="card card-back" aria-label="Business card back">
    <div class="back-lower"></div>
    <div class="back-house" role="img" aria-label="Large pale house illustration"></div>

    <div class="brand">
      <span class="brand-dot"></span>
      <h2 class="brand-name">The Harborline</h2>
    </div>

    <div class="details">
      <ul class="perks">
        <li><svg viewBox="0 0 12 12" aria-hidden="true"><path d="M1 6.5 L4.5 10 L11 1.5" fill="none" stroke="#ffffff" stroke-width="2.2" stroke-linecap="round" stroke-linejoin="round"/></svg>Quality Customer Service</li>
        <li><svg viewBox="0 0 12 12" aria-hidden="true"><path d="M1 6.5 L4.5 10 L11 1.5" fill="none" stroke="#ffffff" stroke-width="2.2" stroke-linecap="round" stroke-linejoin="round"/></svg>Email, text or call welcome</li>
      </ul>
      <p class="person">Dale Merriton</p>
      <p class="contact">Phone: 0400 555 218<br>Email: dale@harborline.net</p>
    </div>
  </section>
</main>
</body>
</html>
```